Design a web site for my business - Brightline Coatings Co.

We are a family business that handles design, fabrication and installation of powder coated aluminum, stainless steel and glass products. Including handrails, privacy slat screens, electric gates and pool fencing. We are based in the Whitsundays in North Queensland and service an area from Airlie Beach to Townsville.

Target Market(s)

Domestic and commercial

Industry/Entity Type

fabrication - manufacturing

Coding

Coded - Design and coding required

Number of Pages Required

5+ page

Colors
0054AA
0677BA
7BADD7
CADEEF
E8F1F8

Requirements
Must have
• photo galleries, contact page, one page for privacy screens, balustrades, glass fencing, stainless steel handrail, powder coated aluminium handrails and pool fencing

```html
<!DOCTYPE html>
<html lang="en">
<head>
<meta charset="utf-8">
<title>Brightline Coatings Co — Architectural Aluminium, Stainless Steel &amp; Glass</title>
<link rel="stylesheet" href="https://fonts.googleapis.com/css2?family=Montserrat:wght@400;500;600;700&family=Open+Sans:wght@400;500&display=swap">
<style>
:root{
  --blue-deep:#0054AA;
  --blue:#0677BA;
  --blue-mid:#7BADD7;
  --blue-light:#CADEEF;
  --blue-pale:#E8F1F8;
  --ink:#141414;
  --muted:#2b2b2b;
  --white:#ffffff;
  --footer:#1c1c1c;
}
*{box-sizing:border-box;margin:0;padding:0}
html,body{width:1200px;height:2625px;overflow:hidden;background:var(--white)}
body{font-family:"Montserrat",sans-serif;color:var(--ink);position:relative}

/* Header */
.site-header{position:absolute;left:0;top:0;width:1200px;height:100px;background:var(--white)}
.brand{position:absolute;left:48px;top:27px;display:flex;align-items:center;gap:14px}
.brand-dot{width:44px;height:44px;border-radius:50%;background:var(--blue)}
.brand-name{font-weight:700;font-size:19px;color:var(--blue-deep);letter-spacing:.3px;white-space:nowrap}
.main-nav{position:absolute;left:398px;top:37px;display:flex;font-family:"Open Sans",sans-serif;font-size:16px;color:var(--ink);white-space:nowrap}
.main-nav a{color:inherit;text-decoration:none;margin-right:18px}
.btn-quote{position:absolute;display:flex;align-items:center;justify-content:center;background:var(--blue);color:var(--white);font-family:"Open Sans",sans-serif;font-size:18px;border-radius:9px;text-decoration:none;white-space:nowrap}
.site-header .btn-quote{left:969px;top:30px;width:182px;height:36px}

/* Hero */
.hero{position:absolute;left:0;top:100px;width:1200px;height:529px;overflow:hidden}
.hero-photo{position:absolute;inset:0;background:
  radial-gradient(ellipse 420px 260px at 1000px 360px,rgba(123,173,215,.75),transparent 70%),
  radial-gradient(ellipse 380px 200px at 820px 120px,rgba(52,92,60,.7),transparent 70%),
  radial-gradient(ellipse 500px 180px at 600px 470px,rgba(92,60,36,.8),transparent 70%),
  linear-gradient(90deg,#050505 0%,#121310 22%,#33362e 42%,#4d5e4e 60%,#6d95ae 80%,#a9cde3 100%)}
.hero-title{position:absolute;left:63px;top:58px;color:var(--white);font-weight:600;font-size:43px;line-height:51px;letter-spacing:.4px}
.hero-tag{position:absolute;left:63px;top:244px;color:var(--white);font-size:18px}
.hero-copy{position:absolute;left:63px;top:304px;color:var(--white);font-size:18px;line-height:23px;white-space:nowrap}

/* Section heads */
.eyebrow{position:absolute;left:0;width:1200px;text-align:center;color:var(--blue)}
.section-title{position:absolute;left:0;width:1200px;text-align:center;color:var(--ink)}

/* Services */
.service{position:absolute;top:750px;width:255px;text-align:center}
.service-photo{width:255px;height:163px}
.service h3{font-weight:500;font-size:17px;margin-top:10px}
.service p{font-size:14px;line-height:17px;margin-top:12px;color:var(--muted)}

/* Why choose */
.why-intro{position:absolute;left:30px;top:1143px;width:1140px;text-align:center;font-weight:500;font-size:18px;line-height:23px}
.why-band{position:absolute;left:0;top:1203px;width:1200px;height:473px;background:var(--blue-pale)}
.why-photo{position:absolute;left:82px;top:21px;width:448px;height:438px;background:
  radial-gradient(ellipse 260px 120px at 220px 300px,rgba(60,44,32,.9),transparent 70%),
  linear-gradient(180deg,#d5dee6 0%,#a9b6c1 28%,#4a3b2e 52%,#5b4a3a 75%,#5d7f69 90%,#6e4b36 100%)}
.feature{position:absolute;width:300px}
.feature h4{font-weight:700;font-size:19px;white-space:nowrap}
.feature p{font-size:14.5px;line-height:17px;margin-top:8px;white-space:nowrap;color:var(--muted)}

/* Process */
.process-band{position:absolute;left:0;top:1846px;width:1200px;height:317px;background:var(--blue-pale)}
.step{position:absolute;top:20px;width:219px}
.step-art{width:219px;height:169px;border-radius:6px;background:linear-gradient(160deg,var(--blue) 0%,var(--blue-deep) 100%)}
.step h3{font-weight:500;font-size:32px;line-height:38px;margin-top:10px;white-space:nowrap;letter-spacing:.5px}
.step p{font-size:14.5px;line-height:17px;margin-top:2px;white-space:nowrap;color:var(--muted)}
.step-arrow{position:absolute;top:212px}

/* Testimonials */
.reviews{position:absolute;left:117px;top:2211px;width:966px;height:263px;border:2px solid var(--blue-mid);border-radius:8px}
.reviews-title{position:absolute;left:340px;top:-14px;padding:0 14px;background:var(--white);font-weight:500;font-size:20px;letter-spacing:.3px;white-space:nowrap}
.review{position:absolute;top:46px;text-align:center}
.stars{display:flex;gap:8px;justify-content:center}
.review blockquote{font-size:18px;line-height:21px;margin-top:18px;color:var(--muted)}
.reviewer{position:absolute;top:176px;font-size:15px;line-height:18px}
.reviewer strong{font-weight:500}

/* Footer */
.site-footer{position:absolute;left:0;top:2495px;width:1200px;height:130px;background:var(--footer);border-top:3px solid #e6e6e6}
.footer-nav{position:absolute;left:170px;top:50px;display:flex;font-family:"Open Sans",sans-serif;font-size:16px;color:#e8e8e8;letter-spacing:.4px;white-space:nowrap}
.footer-nav a{color:inherit;text-decoration:none;margin-right:18px}
.footer-nav a.current{color:#3a3a3a}
.site-footer .btn-quote{left:741px;top:39px;width:182px;height:36px}
</style>
</head>
<body>

<header class="site-header">
  <div class="brand"><span class="brand-dot"></span><span class="brand-name">BRIGHTLINE COATINGS CO</span></div>
  <nav class="main-nav">
    <a href="#">HOME</a><a href="#">ABOUT</a><a href="#">SERVICES</a><a href="#">PROJECTS</a><a href="#">GALLERY</a><a href="#">FAQ</a><a href="#">CONTACT</a>
  </nav>
  <a class="btn-quote" href="#">GET A FREE QUOTE</a>
</header>

<section class="hero">
  <div class="hero-photo" role="img" aria-label="Waterfront boardwalk with timber and aluminium railings beside a rocky bay lined with palm trees"></div>
  <h1 class="hero-title">Architectural<br>Aluminium,<br>Stainless Steel &amp; Glass</h1>
  <p class="hero-tag">Custom Design ◆ fabrication ◆ Installation</p>
  <p class="hero-copy">We work with homeowners, builders, architects and<br>developers to create beautiful, durable outdoor and architectural solutions<br>built for Queensland conditions.</p>
</section>

<p class="eyebrow" style="top:668px;font-size:15px">OUR SERVICES</p>
<h2 class="section-title" style="top:688px;font-weight:700;font-size:29px;left:6px">Complete Architectural Solutions</h2>

<article class="service" style="left:63px">
  <div class="service-photo" role="img" aria-label="Frameless glass balustrade in a tropical garden" style="background:radial-gradient(ellipse 90px 80px at 60px 60px,#1c3520,transparent 80%),linear-gradient(135deg,#22402a,#4d7a48 55%,#a9c0b3)"></div>
  <h3>Glass Balustrades</h3><p>Frameless &amp;<br>semi-frameless glass.</p>
</article>
<article class="service" style="left:340px">
  <div class="service-photo" role="img" aria-label="White aluminium slat electric gate under a blue sky" style="background:linear-gradient(180deg,#1d47b8 0%,#3d6fd1 28%,#e2ded3 40%,#cfcbc1 85%,#9a9a8f 100%)"></div>
  <h3>Electric Gates</h3><p>Automatic sliding and<br>swing gates.</p>
</article>
<article class="service" style="left:617px">
  <div class="service-photo" role="img" aria-label="Timber walkway with stainless steel handrails among rocks and plants" style="background:radial-gradient(ellipse 80px 60px at 140px 110px,#6a4f3e,transparent 80%),linear-gradient(160deg,#27412a,#5b6b4e 45%,#7a6e62 70%,#a49d92)"></div>
  <h3>Handrails</h3><p>Modern aluminium and<br>stainless steel handrails.</p>
</article>
<article class="service" style="left:893px">
  <div class="service-photo" role="img" aria-label="Pavilion roof and powder coated balcony railing" style="background:linear-gradient(180deg,#d3e0ea 0%,#a9bbc8 30%,#3b2f27 55%,#574636 100%)"></div>
  <h3>Powder Coating</h3><p>Premium architectural<br>finishes.</p>
</article>

<p class="eyebrow" style="top:1036px;font-weight:500;font-size:29px;left:6px">Why Choose Us</p>
<h2 class="section-title" style="top:1078px;font-weight:500;font-size:48px;left:4px">Family Owned. Local. Experienced.</h2>
<p class="why-intro">Brightline Coatings Co is a family-owned business specialising in the design, fabrication, powder coating and<br>installation of premium aluminium, stainless steel and glass products.</p>

<section class="why-band">
  <div class="why-photo" role="img" aria-label="Timber pavilion with aluminium balustrade and glass panels"></div>
  <div class="feature" style="left:570px;top:55px"><h4>Family Owned</h4><p>Proudly local and<br>family operated.</p></div>
  <div class="feature" style="left:855px;top:55px"><h4>Premium Powder Coating</h4><p>High quality finishes for<br>long lasting protection</p></div>
  <div class="feature" style="left:570px;top:192px"><h4>Locally Manufactured</h4><p>Proudly local and<br>family operated.</p></div>
  <div class="feature" style="left:855px;top:192px"><h4>Marine Grade Materials</h4><p>Built to withstand our<br>coastal conditions</p></div>
  <div class="feature" style="left:570px;top:330px"><h4>Professional Installation</h4><p style="margin-top:14px">Experienced installers<br>you can rely on</p></div>
  <div class="feature" style="left:855px;top:330px"><h4>Servicing North QLD</h4><p style="margin-top:14px">From Airlie Beach to<br>Townsville</p></div>
</section>

<p class="eyebrow" style="top:1701px;font-weight:500;font-size:30px;left:40px">FEATURE PROJECTS</p>
<h2 class="section-title" style="top:1735px;font-weight:500;font-size:48px;left:-8px">Quality Work. Stunning Results.</h2>
<p class="section-title" style="top:1808px;font-weight:500;font-size:25px;left:-5px">OUR PROCESS</p>

<section class="process-band">
  <div class="step" style="left:134px">
    <div class="step-art" role="img" aria-label="Icon of a client consultation"></div>
    <h3 style="margin-left:7px">Consultation</h3><p style="margin-left:10px">We listen to your<br>ideas and access<br>your needs.</p>
  </div>
  <div class="step" style="left:372px">
    <div class="step-art" role="img" aria-label="Icon of a design drawing board"></div>
    <h3 style="margin-left:56px">Design</h3><p style="margin-left:58px">Wecreate a custom<br>design tailored to<br>your project.</p>
  </div>
  <div class="step" style="left:610px">
    <div class="step-art" role="img" aria-label="Icon of fabrication machinery"></div>
    <h3 style="margin-left:21px">Fabrication</h3><p style="margin-left:23px">Precision Febrication<br>in our local<br>workshop</p>
  </div>
  <div class="step" style="left:848px">
    <div class="step-art" role="img" aria-label="Icon of an installer beside a finished frame"></div>
    <h3 style="margin-left:21px">Installation</h3><p style="margin-left:24px">Profesional<br>installation with<br>attention to detail</p>
  </div>
  <svg class="step-arrow" style="left:382px" width="16" height="12" viewBox="0 0 16 12"><path d="M1 6h12M9 2l4 4-4 4" stroke="#141414" stroke-width="2" fill="none"/></svg>
  <svg class="step-arrow" style="left:579px" width="16" height="12" viewBox="0 0 16 12"><path d="M1 6h12M9 2l4 4-4 4" stroke="#141414" stroke-width="2" fill="none"/></svg>
  <svg class="step-arrow" style="left:830px" width="16" height="12" viewBox="0 0 16 12"><path d="M1 6h12M9 2l4 4-4 4" stroke="#141414" stroke-width="2" fill="none"/></svg>
</section>

<section class="reviews">
  <h2 class="reviews-title">WHAT OUR CLIENTS SAY</h2>
  <svg width="0" height="0" style="position:absolute"><defs><path id="star" d="M10 1l2.6 5.6 6.1.7-4.5 4.2 1.2 6L10 14.5 4.6 17.5l1.2-6L1.3 7.3l6.1-.7z" fill="#0677BA"/></defs></svg>
  <div class="review" style="left:20px;width:230px">
    <div class="stars"><svg width="20" height="19"><use href="#star"/></svg><svg width="20" height="19"><use href="#star"/></svg><svg width="20" height="19"><use href="#star"/></svg><svg width="20" height="19"><use href="#star"/></svg><svg width="20" height="19"><use href="#star"/></svg></div>
    <blockquote>"Excellent workmanship<br>from start to finish."</blockquote>
  </div>
  <div class="reviewer" style="left:51px"><strong>-MARLA P.</strong><br>Airle Beach</div>
  <div class="review" style="left:285px;width:340px">
    <div class="stars"><svg width="20" height="19"><use href="#star"/></svg><svg width="20" height="19"><use href="#star"/></svg><svg width="20" height="19"><use href="#star"/></svg><svg width="20" height="19"><use href="#star"/></svg><svg width="20" height="19"><use href="#star"/></svg></div>
    <blockquote>"Fantastic communication and<br>the finished product looks amazing."</blockquote>
  </div>
  <div class="reviewer" style="left:411px"><strong>-Dean R..</strong><br>Cannonvale</div>
  <div class="review" style="left:655px;width:280px">
    <div class="stars"><svg width="20" height="19"><use href="#star"/></svg><svg width="20" height="19"><use href="#star"/></svg><svg width="20" height="19"><use href="#star"/></svg><svg width="20" height="19"><use href="#star"/></svg><svg width="20" height="19"><use href="#star"/></svg></div>
    <blockquote>"Highly recommend<br>Brightline Coatings Co."</blockquote>
  </div>
  <div class="reviewer" style="left:760px"><strong>Grace W.</strong><br>Bowen</div>
</section>

<footer class="site-footer">
  <nav class="footer-nav">
    <a class="current" href="#">HOME</a><a href="#">ABOUT</a><a href="#">SERVICES</a><a href="#">PROJECTS</a><a href="#">GALLERY</a><a href="#">FAQ</a><a href="#">CONTACT</a>
  </nav>
  <a class="btn-quote" href="#">GET A FREE QUOTE</a>
</footer>

</body>
</html>
```